Customer Value Leaflet

We need a bi-fold brochure designing, based on the attached PDF wireframes. Our company name is brambleharvik.com (of which the logo is currently being designed). The corporate colour is orange (the exact shade of which we are happy to leave to the designers discretion).

The leaflet will distributed to customer experience experts and marketers so the design needs to be bright, engaging, clean and simple. Design is critical.

It Company

```html
<!DOCTYPE html>
<html lang="en">
<head>
<meta charset="utf-8">
<title>BrambleHarvik – We're a Customer Value Company</title>
<link href="https://fonts.googleapis.com/css2?family=Jost:wght@700&family=Open+Sans:wght@300;700&display=swap" rel="stylesheet">
<style>
  :root {
    --brand-orange: #F7941D;
    --ink-white: #FFFFFF;
    --ink-black: #111111;
  }
  * { margin: 0; padding: 0; box-sizing: border-box; }
  html, body {
    width: 1200px;
    height: 1200px;
    overflow: hidden;
    background: var(--brand-orange);
  }
  .leaflet-cover {
    position: relative;
    width: 1200px;
    height: 1200px;
    background: var(--brand-orange);
    color: var(--ink-white);
  }
  .brand-name {
    position: absolute;
    left: 118px;
    top: 92px;
    font-family: "Open Sans", sans-serif;
    font-weight: 700;
    font-size: 42px;
    line-height: 1;
    color: var(--ink-black);
  }
  .ruled-line {
    position: absolute;
    left: 0;
    width: 1200px;
    height: 100px;
  }
  .ruled-line .rule {
    position: absolute;
    top: 47px;
    height: 6px;
    background: var(--ink-white);
  }
  .ruled-line .rule-left { left: 131px; width: 303px; }
  .ruled-line .rule-right { left: 827px; width: 278px; }
  .ruled-line .phrase {
    position: absolute;
    left: 0;
    width: 1200px;
    top: 0;
    height: 100px;
    line-height: 100px;
    text-align: center;
    font-family: "Open Sans", sans-serif;
    font-weight: 300;
    font-size: 70px;
    padding-left: 30px;
  }
  .intro { top: 248px; }
  .outro { top: 928px; }
  .headline {
    position: absolute;
    left: 0;
    width: 1200px;
    text-align: center;
    font-family: "Jost", sans-serif;
    font-weight: 700;
    font-size: 212px;
    line-height: 1;
    letter-spacing: -2px;
    text-transform: uppercase;
  }
  .headline-top { top: 430px; }
  .headline-bottom { top: 652px; padding-left: 10px; }
</style>
</head>
<body>
  <main class="leaflet-cover">
    <div class="brand-name">[BrambleHarvik]</div>

    <div class="ruled-line intro">
      <span class="rule rule-left"></span>
      <span class="phrase">We’re a</span>
      <span class="rule rule-right"></span>
    </div>

    <h1>
      <span class="headline headline-top">Customer</span>
      <span class="headline headline-bottom">Value</span>
    </h1>

    <div class="ruled-line outro">
      <span class="rule rule-left"></span>
      <span class="phrase">company</span>
      <span class="rule rule-right"></span>
    </div>
  </main>
</body>
</html>
```